Modern design company business card design

We are a design oriented construction firm. The owner is an architect and licensed General Contractor and accomplished furniture designer. We do new home construction and large scale remodeling and office design. We would like a design for our new business cards that is clean and modern, but relatable. We like the bright green color of our logo mixed with different shades of grey. We're also open to reinterpreting the logo.

Target Market(s)

Potential design clients,
Construction clients

Industry/Entity Type

Architecture

Contact Information for Business Card

Tall Maple Design | Build Inc. (optional with logo, Inc. optional)Jeffrey MorganOwner (optional)317.555.0148 cell317.431.8056 officejmorgan@greensquareinc.comwww.greensquareinc.com

Font styles to use
Sans Serif
Other font styles liked:
• Avenir

Requirements
Nice to have
• I like designs that have some continuity between the front and back, i.e. similar layouts or graphic elements that wrap around the card. I tend to prefer horizontal over vertical, but that's not a have to. I also tend to prefer white or recycled paper.

```html
<!DOCTYPE html>
<html lang="en">
<head>
<meta charset="utf-8">
<title>Tall Maple Design | Build — Business Card</title>
<link rel="stylesheet" href="https://fonts.googleapis.com/css2?family=Nunito+Sans:wght@400;600;700&display=swap">
<style>
  :root {
    --backdrop: #141414;
    --card: #ffffff;
    --green: #8cc63f;
    --ink: #1a1a1a;
    --grey: #8a8a8a;
    --rule: #e6e6e6;
  }
  * { margin: 0; padding: 0; box-sizing: border-box; }
  html, body { width: 1200px; height: 900px; overflow: hidden; }
  body {
    background: var(--backdrop);
    font-family: "Nunito Sans", Arial, sans-serif;
    position: relative;
  }
  .card {
    position: absolute;
    top: 306px;
    height: 271px;
    background: var(--card);
    border-radius: 12px;
  }
  .card--front { left: 149px; width: 439px; }
  .card--back { left: 608px; width: 441px; }

  .front-brand {
    position: absolute;
    left: 45px; top: 124px;
    display: flex; align-items: center; gap: 8px;
  }
  .front-brand__dot {
    width: 10px; height: 10px; border-radius: 50%;
    background: var(--green);
  }
  .front-brand__name {
    color: var(--green);
    font-weight: 700;
    font-size: 17px;
    line-height: 20px;
    white-space: nowrap;
  }

  .divider {
    position: absolute;
    left: 190px; top: 72px;
    width: 1px; height: 134px;
    background: var(--rule);
  }
  .person { position: absolute; left: 215px; top: 74px; }
  .person__name { color: var(--green); font-weight: 700; font-size: 15px; line-height: 20px; }
  .person__role { color: var(--ink); font-size: 12px; line-height: 16px; margin-left: 2px; }

  .contacts { position: absolute; left: 215px; top: 129px; list-style: none; }
  .contacts li {
    display: flex; align-items: center;
    height: 18px;
    font-size: 11.5px; color: var(--ink);
    white-space: nowrap;
  }
  .contacts svg { width: 10px; height: 10px; margin: 0 11px 0 2px; fill: none; stroke: var(--green); stroke-width: 1.6; }

  .back-brand {
    position: absolute;
    left: 84px; top: 112px;
    display: flex; align-items: flex-start; gap: 12px;
  }
  .back-brand__dot {
    width: 14px; height: 14px; border-radius: 50%;
    background: var(--green);
    margin-top: 9px;
  }
  .wordmark {
    color: var(--grey);
    font-weight: 400;
    text-transform: uppercase;
  }
  .wordmark__name { display: block; font-size: 28px; line-height: 32px; letter-spacing: 2px; }
  .wordmark__line { display: block; font-size: 12px; line-height: 18px; letter-spacing: 1.5px; }
</style>
</head>
<body>
  <section class="card card--front">
    <div class="front-brand">
      <span class="front-brand__dot" aria-hidden="true"></span>
      <span class="front-brand__name">Tall Maple</span>
    </div>
    <div class="divider"></div>
    <div class="person">
      <p class="person__name">Dennis Holloway</p>
      <p class="person__role">Owner</p>
    </div>
    <ul class="contacts">
      <li><svg viewBox="0 0 10 10"><path d="M2 1 L4 3 L3 4 Q4 6 6 7 L7 6 L9 8 L7.5 9.2 Q3 8 0.8 2.5 Z"/></svg>317.555.0172</li>
      <li><svg viewBox="0 0 10 10"><rect x="2.5" y="0.8" width="5" height="8.4" rx="1"/><path d="M4.3 7.4 H5.7"/></svg>317.555.0148</li>
      <li><svg viewBox="0 0 10 10"><rect x="0.8" y="2" width="8.4" height="6" rx="0.6"/><path d="M1 2.4 L5 5.5 L9 2.4"/></svg>dholloway@tallmapleinc.example</li>
      <li><svg viewBox="0 0 10 10"><path d="M4 6 L6 4"/><path d="M3.2 4.8 L1.8 6.2 A1.6 1.6 0 0 0 3.8 8.2 L5.2 6.8"/><path d="M6.8 5.2 L8.2 3.8 A1.6 1.6 0 0 0 6.2 1.8 L4.8 3.2"/></svg>www.tallmapleinc.example</li>
    </ul>
  </section>

  <section class="card card--back">
    <div class="back-brand">
      <span class="back-brand__dot" aria-hidden="true"></span>
      <p class="wordmark">
        <span class="wordmark__name">Tall Maple</span>
        <span class="wordmark__line">Design | Build</span>
      </p>
    </div>
  </section>
</body>
</html>
```